Hollow Thicket, a 3d voxel survival video game needs a card for gaming conventions

I am the lead developer for Hollow Thicket http://www.HollowThicket.example and need a business card to hand out at an indie gaming convention
The card would need to include the game name, website url, my name, position (Lead Developer), e-mail and phone number
The game is a 3d, voxel (with smooth terrain) based survival game with guns and wildlife. The main icon of the game would likely be a grizzly bear but I am willing to accept other designs too.
Attached is a media kit for the game with some images you can use but don't have to its just what little art I can provide. Anything on the website or from the video game can also be used. unrelated art can also be used.
Target Market(s)
Indie Developers/publishers at conferences
Industry/Entity Type
Games
Contact Information for Business Card
Name: Corin Waldrick
Position: Lead Developer
E-mail: Pale_Kettle@mailbox.example
Phone number: 555-372-1186

```html
<!DOCTYPE html>
<html lang="en">
<head>
<meta charset="utf-8">
<title>Hollow Thicket – Business Card</title>
<link rel="stylesheet" href="https://fonts.googleapis.com/css2?family=Source+Sans+3:wght@400;600;700;800&display=swap">
<style>
  :root {
    --backdrop: #161616;
    --card-white: #f7f8fa;
    --brand-red: #8e1212;
    --brand-gold: #a4844a;
    --ink: #2a2a2a;
    --muted-ink: #555555;
    --mist: #e6e9ec;
    --fur-dark: #5a3a20;
    --fur-light: #a06a3e;
    --scene-sky: #6f8fd0;
    --scene-ground: #4d6a5a;
  }
  * { margin: 0; padding: 0; box-sizing: border-box; }
  html, body {
    width: 1200px;
    height: 900px;
    overflow: hidden;
    background: var(--backdrop);
    font-family: "Source Sans 3", Arial, sans-serif;
  }
  .stage {
    position: relative;
    width: 1200px;
    height: 900px;
  }
  .card {
    position: absolute;
    top: 170px;
    width: 346px;
    height: 560px;
    overflow: hidden;
  }
  .card--front { left: 259px; background: var(--card-white); }
  .card--back { left: 631px; }

  /* front side */
  .front-scenery {
    position: absolute;
    inset: 120px 0 0 0;
    background: linear-gradient(180deg, rgba(230,233,236,0) 0%, var(--mist) 45%, #eef0f1 100%);
  }
  .wordmark {
    position: absolute;
    left: 0;
    right: 0;
    text-align: center;
    font-weight: 800;
    text-transform: uppercase;
    color: var(--brand-red);
    letter-spacing: 1px;
  }
  .card--front .wordmark { top: 86px; font-size: 30px; line-height: 36px; }
  .contact {
    position: absolute;
    top: 180px;
    left: 0;
    right: 0;
    text-align: center;
    color: var(--ink);
  }
  .contact__name {
    font-size: 20px;
    font-weight: 600;
    text-transform: uppercase;
    line-height: 24px;
  }
  .contact__first { color: var(--brand-red); }
  .contact__last { color: var(--brand-gold); }
  .contact__role { font-size: 16px; line-height: 20px; }
  .contact__lines { margin-top: 36px; font-size: 16px; line-height: 20px; }
  .contact__label { color: var(--brand-red); font-weight: 700; margin-right: 4px; }
  .contact__url { font-size: 13px; line-height: 18px; margin-top: 2px; color: var(--muted-ink); }
  .front-bear {
    position: absolute;
    left: 0;
    top: 340px;
    width: 222px;
    height: 220px;
    border-radius: 40% 55% 0 0;
    background: radial-gradient(ellipse at 60% 40%, var(--fur-light) 0%, var(--fur-dark) 75%);
  }

  /* back side */
  .back-scene {
    position: absolute;
    inset: 0;
    background: linear-gradient(180deg, var(--scene-sky) 0%, var(--scene-ground) 100%);
  }
  .back-bear {
    position: absolute;
    left: 0;
    top: 250px;
    width: 250px;
    height: 310px;
    border-radius: 45% 45% 0 0;
    background: radial-gradient(ellipse at 55% 35%, #b07c4c 0%, var(--fur-dark) 80%);
  }
  .card--back .wordmark {
    top: 100px;
    font-size: 52px;
    line-height: 52px;
  }
</style>
</head>
<body>
<main class="stage">
  <section class="card card--front">
    <div class="front-scenery" role="img" aria-label="Faint misty forest with pine trees and mountains"></div>
    <div class="wordmark">Hollow Thicket</div>
    <div class="contact">
      <p class="contact__name"><span class="contact__first">Corin</span> <span class="contact__last">Waldrick</span></p>
      <p class="contact__role">Lead Developer</p>
      <div class="contact__lines">
        <p><span class="contact__label">P:</span>555-372-1186</p>
        <p><span class="contact__label">E:</span>Pale_Kettle@mailbox.example</p>
        <p class="contact__url">http://www.HollowThicket.example</p>
      </div>
    </div>
    <div class="front-bear" role="img" aria-label="Roaring grizzly bear photograph"></div>
  </section>

  <section class="card card--back">
    <div class="back-scene" role="img" aria-label="In-game landscape with sky, pine trees, hills and a river"></div>
    <div class="back-bear" role="img" aria-label="Grizzly bear standing on a rock by the river"></div>
    <div class="wordmark">Hollow<br>Thicket</div>
  </section>
</main>
</body>
</html>
```